Medical centre needs a business card

We are a medcial centre in Australia, needing a new business card. Our demographic is low working class families. We are going to be renovating our premises to modernise the look and also had a new logo done a few months ago representing quality and community, and now need to update our cards. It needs to be doubled sided, with logo and contact details on the front, and appointment details on the back. . Needs to be modern and simple, easy to read. <br/><br/>Name: Kindle Grove Medical Centre <br/>Address: 512 Parmley Rd (Cnr Parmley Rd & Osgood Creek Rd),<br/>Tindarra Court Shopping Centre, Marrindale, KG 9012<br/>Ph: 08 8461 3072<br/>Tag line: Where your wellbeing comes first<br/>Website: www.kindlegrovemedicalcentre-example.com.au<br/>Online bookings also available<br/><br/>(On the back, to have 3 lines of appointments that can be written in.<br/>Day, date, time)<br/><br/>Your next appointment is on<br/>Can try “M T W Th F Sa Su _________________ at ____________ am/pm” or other combinations <br/>Please advise as soon as possible if unable to attend<br/>Cancellation fees apply if less than 2 hrs notice<br/>Online appointments available (please highlight this option by either by position, colour or font)

Target Market(s)

Lower social economic working class, young families to seniors

Industry/Entity Type

Medical Centre

Contact Information for Business Card

Kindle Grove Medical Centre
512 Parmley Rd (Cnr Parmley Rd & Osgood Creek Drive)
Tindarra Court Shopping Centre
Paralowie SA 5108
Ph: 08 8461 3072
www.kindlegrovemedicalcentre-example.com.au
Tagline line: where your wellbeing comes first
Back side is for appointments
Your next appointment is with Dr ______________
Day/date/time (Please give 3 lines of appointments)
Please advise as soon as possible if unable to attend
Cancellation fees apply if less than 2 hours notice
Online appointments available
Book online easily and conveniently (please highlight online appointments)

Font styles to use
Serif
Sans Serif

Colors

Designer to choose colors to be used in the design.

Requirements
Must have
• Modern and simple
• Easy to ready
• Induces a wellbeing feeling
• Incorporate our logo colours and feel from logo
• Induces feeling of stability and security
Nice to have
• Attract attention
• Pleasant to look at
• Feeling of innovation
Should not have
• Loud clashing colours
• Overly luxurious feeling
• Overly artistic

```html
<!DOCTYPE html>
<html lang="en">
<head>
<meta charset="utf-8">
<title>Kindle Grove Medical Centre – Business Card</title>
<link href="https://fonts.googleapis.com/css2?family=Montserrat:wght@400;500;600;700&display=swap" rel="stylesheet">
<style>
  :root {
    --blue: #0a6bb8;
    --green: #8cc63f;
    --ink: #1d1d1f;
    --paper: #ffffff;
    --stage: #e9ebee;
    --wash-blue: #dcebf7;
    --wash-green: #eef5df;
  }
  * { box-sizing: border-box; margin: 0; padding: 0; }
  html, body { width: 1200px; height: 900px; overflow: hidden; }
  body {
    background: var(--stage);
    font-family: "Montserrat", sans-serif;
    color: var(--ink);
    position: relative;
  }
  .card {
    position: absolute;
    left: 260px;
    width: 680px;
    height: 415px;
    background: var(--paper);
    border-radius: 18px;
    overflow: hidden;
    box-shadow: 0 6px 18px rgba(0,0,0,.12);
  }
  .card--back { top: 22px; }
  .card--front { top: 463px; }

  /* Back: appointment side */
  .appt-title {
    position: absolute; left: 40px; top: 30px; width: 600px; height: 52px;
    border: 2px solid var(--green);
    display: flex; align-items: center; justify-content: center;
    color: var(--blue); font-weight: 700; font-size: 21px; letter-spacing: 2px;
  }
  .field {
    position: absolute; left: 34px; right: 34px;
    display: flex; align-items: flex-end; gap: 8px;
    color: var(--blue); font-weight: 600; font-size: 17px;
  }
  .field .line { flex: 1; border-bottom: 1.5px solid var(--green); height: 1px; }
  .field .line--short { flex: 0 0 60px; }
  .field .line--mid { flex: 0 0 110px; }
  .field--name { top: 100px; }
  .field--date { top: 148px; }
  .days {
    position: absolute; left: 34px; right: 34px; top: 196px;
    display: flex; justify-content: space-between;
    color: var(--blue); font-weight: 600; font-size: 14px;
  }
  .day { display: flex; align-items: center; gap: 7px; }
  .day-box { width: 12px; height: 12px; border: 1.5px solid var(--green); flex: none; }
  .notice {
    position: absolute; left: 34px; right: 34px; top: 238px;
    color: var(--blue); font-size: 16.5px; letter-spacing: 1px; line-height: 1.55;
  }
  .online-band {
    position: absolute; left: 0; right: 0; bottom: 0; height: 76px;
    background: var(--blue);
    display: flex; align-items: center; justify-content: center;
    color: #fff; font-weight: 600; font-size: 21px; letter-spacing: 8px;
  }

  /* Front: contact side */
  .watermark {
    position: absolute; left: 0; top: 90px; width: 340px; height: 250px;
    background: radial-gradient(ellipse at 40% 50%, var(--wash-green) 0%, var(--wash-blue) 55%, rgba(255,255,255,0) 80%);
    opacity: .8;
  }
  .brand {
    position: absolute; left: 34px; top: 38px;
    display: flex; align-items: center; gap: 10px;
    color: var(--blue); font-weight: 700; font-size: 19px; letter-spacing: .5px;
  }
  .brand-dot { width: 16px; height: 16px; border-radius: 50%; background: var(--green); }
  .contact {
    position: absolute; right: 40px; top: 96px; text-align: right;
  }
  .person { color: var(--green); font-weight: 600; font-size: 38px; letter-spacing: 1px; line-height: 1; }
  .role { font-size: 20px; letter-spacing: 1.5px; margin-top: 6px; }
  .address { font-size: 19px; letter-spacing: 1.2px; line-height: 1.3; margin-top: 14px; }
  .contact-row {
    display: flex; justify-content: flex-end; align-items: center; gap: 10px;
    font-size: 18px; letter-spacing: 1px; margin-top: 10px; white-space: nowrap;
  }
  .contact-row svg { width: 16px; height: 16px; flex: none; }
  .tagline-row {
    position: absolute; left: 0; right: 0; bottom: 34px;
    display: flex; align-items: center; gap: 14px; padding-right: 34px;
  }
  .tagline-rule { height: 2px; background: var(--green); }
  .tagline-rule--left { width: 120px; flex: none; }
  .tagline-rule--right { flex: 1; }
  .tagline { color: var(--blue); font-weight: 500; font-size: 21px; letter-spacing: 1px; white-space: nowrap; }
</style>
</head>
<body>

<section class="card card--back" aria-label="Appointment side">
  <div class="appt-title">YOUR NEXT APPOINTMENT</div>
  <div class="field field--name"><span>Name :</span><span class="line"></span></div>
  <div class="field field--date">
    <span>Date :</span><span class="line line--short"></span><span>/</span><span class="line line--short"></span><span>/</span><span class="line line--mid"></span>
    <span>&nbsp;Time :</span><span class="line"></span><span>AM/PM</span>
  </div>
  <div class="days">
    <span class="day"><span class="day-box"></span>MON</span>
    <span class="day"><span class="day-box"></span>TUE</span>
    <span class="day"><span class="day-box"></span>WED</span>
    <span class="day"><span class="day-box"></span>THU</span>
    <span class="day"><span class="day-box"></span>FRI</span>
    <span class="day"><span class="day-box"></span>SAT</span>
    <span class="day"><span class="day-box"></span>SUN</span>
  </div>
  <p class="notice">Please advise as soon as possible if unable to attend<br>Cancellation fees apply if less than 2 hours notice.</p>
  <div class="online-band">ONLINE APPOINTMENTS AVAILABLE</div>
</section>

<section class="card card--front" aria-label="Contact side">
  <div class="watermark" role="img" aria-label="Faint brand decoration area"></div>
  <div class="brand"><span class="brand-dot"></span><span>Kindle Grove Medical Centre</span></div>
  <div class="contact">
    <div class="person">MARCUS FELDON</div>
    <div class="role">Manager</div>
    <div class="address">
      512 Parmley Rd<br>
      Tindarra Court Shopping Centre<br>
      Marrindale, KG 9012
    </div>
    <div class="contact-row">
      <span>08 8461 3072</span>
      <svg viewBox="0 0 24 24" aria-hidden="true"><path fill="#8cc63f" d="M6.6 10.8a15 15 0 0 0 6.6 6.6l2.2-2.2c.3-.3.7-.4 1-.2 1.1.4 2.3.6 3.6.6.6 0 1 .4 1 1V20c0 .6-.4 1-1 1A17 17 0 0 1 3 4c0-.6.4-1 1-1h3.5c.6 0 1 .4 1 1 0 1.3.2 2.5.6 3.6.1.3 0 .7-.2 1z"/></svg>
    </div>
    <div class="contact-row">
      <span>www.kindlegrovemedicalcentre-example.com.au</span>
      <svg viewBox="0 0 24 24" aria-hidden="true"><g fill="none" stroke="#8cc63f" stroke-width="2"><circle cx="12" cy="12" r="9"/><ellipse cx="12" cy="12" rx="4" ry="9"/><path d="M3 12h18M5 7h14M5 17h14"/></g></svg>
    </div>
  </div>
  <div class="tagline-row">
    <span class="tagline-rule tagline-rule--left"></span>
    <span class="tagline">Where Your Wellbeing Comes First</span>
    <span class="tagline-rule tagline-rule--right"></span>
  </div>
</section>

</body>
</html>
```